Need Business Card ASAP

We need a business card design for a meeting coming up in a few days. The company name is Harlow Ridge Building and Construction and the logo is attached. Something clean, cool, and contemporary that we can get to a printer right away. Attached is the business card for Volmar Energy, an affiliated company, which we like. Instead of the hawk on the back, you could use the attached "D". We'll also be needing matching letterhead in the near future, so ideas for that are welcome.

```html
<!DOCTYPE html>
<html lang="en">
<head>
<meta charset="utf-8">
<title>Harlow Ridge Building and Construction – Business Card</title>
<link rel="stylesheet" href="https://fonts.googleapis.com/css2?family=Open+Sans:wght@400;600;700&display=swap">
<style>
  :root {
    --backdrop: #e9e6df;
    --card-white: #ffffff;
    --card-dark: #3d3d3d;
    --ink: #1b1b1b;
    --gold: #b9b38a;
    --gold-light: #d6d1b0;
    --text: #222222;
    --muted: #777777;
  }
  * { margin: 0; padding: 0; box-sizing: border-box; }
  html, body {
    width: 1034px; height: 1200px; overflow: hidden;
    background: var(--backdrop);
    font-family: "Open Sans", Arial, sans-serif;
  }
  .card {
    position: absolute; left: 71px; width: 887px;
    box-shadow: 0 4px 14px rgba(0,0,0,.18);
  }
  .card-front { top: 64px; height: 510px; background: var(--card-white); }
  .card-back  { top: 613px; height: 553px; background: var(--card-dark); }

  .bar { position: absolute; height: 14px; }
  .bar-top-left     { top: 0;     left: 0;     width: 365px; background: var(--ink); }
  .bar-top-right    { top: 0;     left: 395px; width: 492px; background: var(--gold); }
  .bar-bottom-left  { top: 371px; left: 0;     width: 365px; background: var(--gold); }
  .bar-bottom-right { top: 371px; left: 395px; width: 492px; background: var(--ink); }

  .brand-block {
    position: absolute; left: 160px; top: 71px; width: 183px; height: 247px;
    background: var(--ink);
    display: flex; flex-direction: column; justify-content: center;
    padding: 0 16px; gap: 4px;
  }
  .brand-name {
    color: var(--gold); font-weight: 600; font-size: 22px; line-height: 1.25;
    text-align: center;
  }

  .divider {
    position: absolute; left: 375px; top: 71px; width: 3px; height: 250px;
    background: linear-gradient(to bottom, transparent, #9a9a9a 40%, #9a9a9a 60%, transparent);
  }

  .identity { position: absolute; left: 402px; top: 64px; }
  .person-name { color: var(--gold); font-weight: 700; font-size: 34px; line-height: 1.2; }
  .person-title { color: var(--muted); font-weight: 700; font-size: 22px; margin-top: 2px; }

  .contacts { position: absolute; left: 402px; top: 153px; list-style: none; }
  .contacts li {
    display: flex; align-items: center; gap: 10px;
    font-size: 25px; color: var(--text); height: 41px;
  }
  .contacts svg { width: 20px; height: 20px; flex: none; }

  .company-footer {
    position: absolute; left: 0; right: 0; top: 410px; text-align: center;
  }
  .company-name { color: var(--gold); font-weight: 700; font-size: 29px; }
  .company-address { color: var(--ink); font-size: 21px; margin-top: 4px; }

  .back-mark {
    position: absolute; left: 0; right: 0; top: 200px;
    display: flex; justify-content: center; align-items: center; gap: 22px;
  }
  .back-mark .square { width: 40px; height: 40px; background: var(--gold); }
  .back-mark .name {
    color: var(--card-white); font-weight: 600; font-size: 48px; letter-spacing: 1px;
  }
  .back-web {
    position: absolute; left: 0; right: 0; top: 442px; text-align: center;
    color: var(--card-white); font-weight: 700; font-size: 27px; letter-spacing: 2px;
  }
</style>
</head>
<body>
  <section class="card card-front">
    <div class="bar bar-top-left"></div>
    <div class="bar bar-top-right"></div>

    <div class="brand-block">
      <span class="brand-name">Harlow Ridge Building and Construction</span>
    </div>

    <div class="divider"></div>

    <div class="identity">
      <p class="person-name">Your Name</p>
      <p class="person-title">Title</p>
    </div>

    <ul class="contacts">
      <li>
        <svg viewBox="0 0 20 20" aria-hidden="true"><path d="M5 2 L8 6 L6.5 8 Q8 12 12 13.5 L14 12 L18 15 L16 18 Q6 17 2 5 Z" fill="#333"/></svg>
        (123) 456-7890
      </li>
      <li>
        <svg viewBox="0 0 20 20" aria-hidden="true"><rect x="6" y="1" width="9" height="18" rx="1.5" fill="#333"/><rect x="7.5" y="4" width="6" height="7" fill="#fff"/></svg>
        (123) 456-7890
      </li>
      <li>
        <svg viewBox="0 0 20 20" aria-hidden="true"><rect x="2" y="5" width="16" height="11" fill="#333"/><path d="M2 5 L10 11 L18 5" stroke="#fff" stroke-width="1.4" fill="none"/></svg>
        yourname@harlowridge.com
      </li>
      <li>
        <svg viewBox="0 0 20 20" aria-hidden="true"><circle cx="10" cy="10" r="8" fill="none" stroke="#333" stroke-width="1.6"/><ellipse cx="10" cy="10" rx="3.5" ry="8" fill="none" stroke="#333" stroke-width="1.3"/><path d="M2 10 H18" stroke="#333" stroke-width="1.3"/></svg>
        www.harlowridge.com
      </li>
    </ul>

    <div class="bar bar-bottom-left"></div>
    <div class="bar bar-bottom-right"></div>

    <div class="company-footer">
      <p class="company-name">Harlow Ridge Building and Construction</p>
      <p class="company-address">00, Complex Name, Street, City 00000</p>
    </div>
  </section>

  <section class="card card-back">
    <div class="back-mark">
      <span class="square"></span>
      <span class="name">Harlow Ridge</span>
    </div>
    <p class="back-web">www.harlowridgebuilding.com</p>
  </section>
</body>
</html>
```